Tessel Mobile website

Hello. Pray all is well. Peace be with you.

looking to make a website with pages information from https://veradilo.us. English and Spanish.

the header of quarnetel.com when in mobile version

clean vector images and layout of fendlecell.com

and the clean simple black and white look of tavesport.com

please use the attached logo for color guidance

also need the my account section for users to be designed

there should also be a countdown timer for days:hours:seconds on the home page

please do website in figma

```html
<!DOCTYPE html>
<html lang="en">
<head>
<meta charset="utf-8">
<title>Tessel Mobile</title>
<link href="https://fonts.googleapis.com/css2?family=Lato:ital,wght@0,400;0,700;0,900;1,700&display=swap" rel="stylesheet">
<style>
:root{
  --green:#3dab76;
  --green-dark:#2f8f60;
  --mint:#e2f9ef;
  --mint-bar:#e8faf1;
  --ink:#1b1b1b;
  --muted:#555;
  --line:#cfe9dc;
  --grey-card:#eeeeee;
  --black:#0d0d0d;
  --star:#f08a24;
}
*{box-sizing:border-box;margin:0;padding:0}
html,body{width:1200px;height:5195px;overflow:hidden;background:#fff}
body{font-family:'Lato',sans-serif;color:var(--ink);position:relative}
.abs{position:absolute}
.btn{position:absolute;background:var(--green);color:#fff;font-weight:700;font-size:14px;display:flex;align-items:center;justify-content:center;border-radius:3px}
.accent{color:var(--green)}
.sec-title{position:absolute;left:0;width:1200px;text-align:center;font-weight:900;font-size:38px;letter-spacing:-.3px}
.sec-sub{position:absolute;left:0;width:1200px;text-align:center;font-size:14px;line-height:22px;color:#444}
.art{position:absolute}

/* top bar + nav */
.topbar{left:0;top:0;width:1200px;height:40px;background:var(--mint-bar);font-size:14px;display:flex;align-items:center;justify-content:center}
.nav a{position:absolute;font-size:14px;color:var(--ink);text-decoration:none}
.nav .home{background:var(--green);color:#fff;padding:7px 9px;border-radius:3px}
.brand{position:absolute;left:520px;top:56px;width:160px;text-align:center}
.brand .mark{width:48px;height:48px;background:var(--ink);margin:0 auto 4px}
.brand .name{font-weight:700;font-size:19px;color:var(--ink)}

/* hero */
.hero{left:34px;top:155px;width:1132px;height:600px;background:var(--mint);border-radius:20px}
.hero h1{position:absolute;left:77px;top:116px;font-size:52px;font-weight:900;line-height:70px}
.hero p{position:absolute;left:77px;top:283px;width:520px;font-size:21px;line-height:31px;color:#333}
.dots{position:absolute;left:528px;top:538px;display:flex;gap:5px}
.dots i{width:11px;height:11px;border-radius:50%;background:#6b6b6b;display:block}

/* features */
.feature{position:absolute;top:965px;width:230px;text-align:center}
.feature svg{display:block;margin:0 auto 10px}
.feature h4{font-size:14px;font-weight:700;line-height:20px}
.feature p{font-size:14px;line-height:21px;color:#444}

/* plan cards */
.promo{position:absolute;top:1230px;width:472px;height:222px;border:1.5px solid var(--line);border-radius:12px;overflow:hidden}
.promo h3{position:absolute;top:20px;width:100%;text-align:center;font-size:38px;font-weight:900}
.promo p{position:absolute;top:74px;left:40px;width:392px;text-align:center;font-size:14px;line-height:21px;color:#444}

/* deals */
.deal-photo{position:absolute;border-radius:8px}
.deal h3{position:absolute;font-size:26px;font-weight:700;line-height:34px}
.deal p{position:absolute;font-size:14px;line-height:25px;color:#444}

/* testimonials */
.band{left:0;top:2473px;width:1200px;height:500px;background:var(--green)}
.review{position:absolute;top:191px;width:317px;height:226px;background:#fff;border-radius:4px;padding:34px 24px}
.review.dark{background:var(--green-dark);color:#fff}
.review .stars{color:var(--star);font-size:17px;letter-spacing:1px}
.review.dark .stars{color:#fff}
.review p{font-size:14px;line-height:22px;margin-top:10px;color:#444}
.review.dark p{color:#eaf7f0}
.review b{display:block;margin-top:16px;font-size:16px}
.review small{font-size:12px;color:#555}
.review.dark small{color:#dff}

/* steps */
.step{position:absolute;top:3181px;width:234px;height:177px;border-radius:6px;text-align:center;padding-top:30px;background:var(--grey-card)}
.step.on{background:var(--green);color:#fff}
.step h4{font-size:14px;font-weight:700;color:var(--green);line-height:20px;margin:10px 14px 4px}
.step.on h4{color:#fff}
.step p{font-size:12px;line-height:16px;color:#555;margin:0 20px}
.step.on p{color:#e6f7ee}
.step svg{display:block;margin:0 auto}

/* faq */
.faq{position:absolute;left:631px;width:458px;border:1px solid #ddd;border-radius:4px;font-size:14px;background:#fafafa}
.faq .q{height:60px;display:flex;align-items:center;justify-content:space-between;padding:0 24px 0 28px}
.faq .q span:last-child{font-size:22px}
.faq.open .q{color:var(--green);background:#f3faf6}
.faq .a{padding:14px 18px 20px;font-size:15px;line-height:22px;color:#333;background:#fff}

/* blog */
.post{position:absolute;top:4276px;width:317px;text-align:center}
.post .ph{height:232px;border-radius:8px}
.post h4{margin-top:28px;font-size:21px;line-height:30px;font-weight:700}
.post p{margin-top:12px;font-size:14px;line-height:22px;color:#444;padding:0 18px}
.post em{display:block;margin-top:16px;font-size:14px;font-weight:700;color:var(--green)}
.arrow{position:absolute;top:4381px;width:32px;height:32px;border-radius:50%;background:var(--green);display:flex;align-items:center;justify-content:center}

/* footer */
.footer{left:0;top:4780px;width:1200px;height:415px;background:var(--black);color:#fff}
.fcol{position:absolute;top:85px}
.fcol h5{font-size:19px;font-weight:700;margin-bottom:22px}
.fcol a{display:block;color:#e6e6e6;font-size:14px;text-decoration:none;margin-bottom:17px}
.fcol p{font-size:14px;line-height:26px;color:#e6e6e6;width:260px}
.social{display:flex;gap:14px;margin-top:26px;align-items:center}
.social i{display:block;width:22px;height:22px;border:2px solid #fff;border-radius:4px}
.social i.on{width:34px;height:34px;background:var(--green);border-color:var(--green)}
.copy{position:absolute;top:378px;left:0;width:1200px;text-align:center;font-size:12px;color:#ddd}
</style>
</head>
<body>

<div class="abs topbar">Welcome to Tessel Mobile</div>

<nav class="nav">
  <a class="home" style="left:111px;top:84px">Home</a>
  <a style="left:187px;top:91px">Bring Your Own phone</a>
  <a style="left:367px;top:91px">Coverage Check</a>
  <a style="left:739px;top:91px">About Us</a>
  <a style="left:829px;top:91px">Support</a>
  <a style="left:910px;top:91px">Blog</a>
  <svg class="abs" style="left:968px;top:84px" width="20" height="22" viewBox="0 0 20 22"><circle cx="10" cy="6" r="5" fill="#3dab76"/><path d="M1 21c0-6 4-9 9-9s9 3 9 9z" fill="#3dab76"/></svg>
  <a class="home" style="left:1009px;top:78px;width:80px;text-align:center;padding:9px 0">En ⌄</a>
</nav>
<div class="brand"><div class="mark"></div><div class="name">tessel mobile</div></div>

<section class="abs hero">
  <h1>Stay Connected.<br>Anywhere. Anytime.</h1>
  <p>Tessel Mobile gives you fast, reliable, and affordable wireless service — without contracts, hidden fees, or surprises.</p>
  <div class="btn" style="left:77px;top:415px;width:152px;height:42px">Shop Now</div>
  <div class="art" role="img" aria-label="Cartoon panda mascot holding a phone showing a plan offer" style="left:600px;top:40px;width:520px;height:470px;border-radius:40%;background:radial-gradient(ellipse at center,#d9d9d9 0%,#8a8a8a 45%,rgba(226,249,239,0) 72%)"></div>
  <div class="dots"><i></i><i></i><i></i><i></i></div>
</section>

<h2 class="sec-title" style="top:832px">Why Choose <span class="accent">Tessel Mobile</span></h2>
<p class="sec-sub" style="top:892px">Experience wireless the way it should be — simple, honest, and built for you. No contracts.<br>No hidden fees. Just powerful connectivity in English and Spanish.</p>

<div class="feature" style="left:97px">
  <svg width="58" height="46" viewBox="0 0 58 46" fill="none" stroke="#3dab76" stroke-width="2"><rect x="12" y="10" width="26" height="20"/><path d="M38 16h10l6 8v6H38z"/><circle cx="20" cy="34" r="5"/><circle cx="46" cy="34" r="5"/><path d="M2 14h8M4 20h8M6 26h6"/></svg>
  <h4>Free 2-Day Shipping,<br>Seriously!</h4>
  <p>Get your SIM delivered fast and free — because waiting is so last year.</p>
</div>
<div class="feature" style="left:359px">
  <svg width="58" height="46" viewBox="0 0 58 46" fill="none" stroke="#3dab76" stroke-width="2"><rect x="10" y="14" width="32" height="22" rx="3"/><path d="M10 21h32M16 30h10"/><circle cx="44" cy="12" r="9"/><path d="M40 12l3 3 5-6"/></svg>
  <h4>No Credit Checks, No<br>Stress</h4>
  <p>We keep it simple — no hoops, no paperwork, just mobile freedom.</p>
</div>
<div class="feature" style="left:621px">
  <svg width="58" height="46" viewBox="0 0 58 46" fill="none" stroke="#3dab76" stroke-width="2"><circle cx="29" cy="25" r="19"/><circle cx="29" cy="25" r="13"/><path d="M29 25l8-8"/><circle cx="29" cy="25" r="2" fill="#3dab76"/></svg>
  <h4>5G Speed at Full<br>Throttle!</h4>
  <p>Full-speed 5G data that keeps up with your life — and then some. We're not slowing down</p>
</div>
<div class="feature" style="left:883px">
  <svg width="58" height="46" viewBox="0 0 58 46" fill="none" stroke="#3dab76" stroke-width="2"><rect x="6" y="6" width="38" height="32" rx="2"/><path d="M6 14h38M14 2v8M36 2v8M12 20h4M20 20h4M28 20h4M12 28h4M20 28h4"/><circle cx="44" cy="34" r="9"/><path d="M40 34l3 3 5-6"/></svg>
  <h4>Zero Annual Contracts,<br>Zero Hassles!</h4>
  <p>Month-to-month freedom — stay as long as you love us (and you will).</p>
</div>

<div class="promo" style="left:111px">
  <h3>Our <span class="accent">Plans</span></h3>
  <p>Excepteur sint occaecat cupidatat non proident, sunt in culpa qui officia deserunt mollit anim id est laborum.</p>
  <div class="btn" style="left:179px;top:134px;width:150px;height:42px">Choose a Plan</div>
  <div class="art" role="img" aria-label="Panda mascot peeking from the corner" style="left:8px;top:120px;width:130px;height:102px;border-radius:50% 50% 0 0;background:linear-gradient(#e8e8e8,#555)"></div>
</div>
<div class="promo" style="left:617px">
  <h3>Our <span class="accent">Phones</span></h3>
  <p>Excepteur sint occaecat cupidatat non proident, sunt in culpa qui officia deserunt mollit anim id est laborum.</p>
  <div class="btn" style="left:179px;top:134px;width:150px;height:42px">Shop Now</div>
  <div class="art" role="img" aria-label="Panda mascot peeking from the corner" style="left:336px;top:120px;width:130px;height:102px;border-radius:50% 50% 0 0;background:linear-gradient(#e8e8e8,#555)"></div>
</div>

<h2 class="sec-title" style="top:1532px">Hot Deals And Benefits <span class="accent">You Can't Miss</span></h2>
<p class="sec-sub" style="top:1592px">Duis aute irure dolor in reprehenderit in voluptate velit esse<br>cillum dolore eu fugiat nulla pariatur.</p>

<div class="deal">
  <div class="deal-photo" role="img" aria-label="Smiling woman checking her phone on a city street" style="left:111px;top:1684px;width:470px;height:327px;background:linear-gradient(135deg,#d8cfc3,#a48d78 55%,#b04a2c)"></div>
  <h3 style="left:686px;top:1734px">Bring your Own Phone and use it<br>with Tessel Mobile</h3>
  <p style="left:686px;top:1828px;width:400px">Love your phone? Keep it. Just pop in a SIM and you're good to go — no extra steps, no weird settings.</p>
  <div class="btn" style="left:686px;top:1909px;width:192px;height:42px">Check Compatibility</div>
  <div class="art" role="img" aria-label="Standing panda mascot" style="left:965px;top:1870px;width:125px;height:126px;border-radius:45%;background:radial-gradient(#d8d8d8,#444 70%,rgba(255,255,255,0) 72%)"></div>

  <h3 style="left:111px;top:2094px">Shop a New Phone: Nova<br>15 Pro</h3>
  <p style="left:111px;top:2188px;width:420px">Upgrade to the ultimate performance and power. The Nova 15 Pro is here — lightning fast, stunningly sleek, and ready for your Tessel Mobile plan.</p>
  <div class="btn" style="left:111px;top:2292px;width:195px;height:42px">Shop Nova 15 Pro</div>
  <div class="deal-photo" role="img" aria-label="Couple browsing phones in a bright electronics store" style="left:617px;top:2055px;width:472px;height:327px;background:linear-gradient(135deg,#e8e4df,#9a8474 55%,#3c4a63)"></div>
  <div class="art" role="img" aria-label="Panda mascot peeking up" style="left:30px;top:2374px;width:135px;height:100px;border-radius:50% 50% 0 0;background:linear-gradient(#e6e6e6,#555)"></div>
</div>

<section class="abs band">
  <h2 class="sec-title" style="top:59px;color:#fff">What Our Customers Say</h2>
  <p class="sec-sub" style="top:119px;color:#eef">Duis aute irure dolor in reprehenderit in voluptate velit esse<br>cillum dolore eu fugiat nulla pariatur.</p>
  <div class="review" style="left:111px"><div class="stars">★★★★★</div><p>Excepteur sint occaecat cupidatat non proident, sunt in culpa qui officia deserunt mollit anim id est laborum.</p><b>Watterson</b><small>Apr 05 2025</small></div>
  <div class="review dark" style="left:442px"><div class="stars">★★★★★</div><p>Excepteur sint occaecat cupidatat non proident, sunt in culpa qui officia deserunt mollit anim id est laborum.</p><b>Mary</b><small>Apr 05 2025</small></div>
  <div class="review" style="left:772px"><div class="stars">★★★★★</div><p>Excepteur sint occaecat cupidatat non proident, sunt in culpa qui officia deserunt mollit anim id est laborum.</p><b>Geraldine</b><small>Apr 05 2025</small></div>
</section>

<h2 class="sec-title" style="top:3050px">Easy Activation <span class="accent">Process</span></h2>
<p class="sec-sub" style="top:3110px">Duis aute irure dolor in reprehenderit in voluptate velit esse<br>cillum dolore eu fugiat nulla pariatur.</p>
<div class="art" role="img" aria-label="Standing panda mascot" style="left:1005px;top:3018px;width:100px;height:150px;border-radius:45%;background:radial-gradient(#ddd,#444 68%,rgba(255,255,255,0) 70%)"></div>

<div class="step" style="left:111px">
  <svg width="40" height="40" viewBox="0 0 40 40" fill="none" stroke="#3dab76" stroke-width="2"><path d="M20 37s-11-12-11-20a11 11 0 0 1 22 0c0 8-11 20-11 20z"/><circle cx="20" cy="17" r="4"/></svg>
  <h4>Check CoverageIn Your Area</h4><p>Risus commodo viverra aecenas accumsan lacus vel facilisis.</p>
</div>
<div class="step on" style="left:359px">
  <svg width="40" height="40" viewBox="0 0 40 40" fill="none" stroke="#fff" stroke-width="2"><rect x="12" y="3" width="16" height="30" rx="3"/><path d="M18 28h4M6 30l6 6h14"/></svg>
  <h4>Bring Your Phone or Get a New One</h4><p>Risus commodo viverra aecenas accumsan lacus vel facilisis.</p>
</div>
<div class="step" style="left:607px">
  <svg width="40" height="40" viewBox="0 0 40 40" fill="none" stroke="#3dab76" stroke-width="2"><rect x="8" y="5" width="24" height="32" rx="2"/><path d="M14 5V2h12v3M13 15l2 2 4-4M13 25l2 2 4-4M22 16h6M22 26h6"/></svg>
  <h4>Choose the PlanYou Like Best</h4><p>Risus commodo viverra aecenas accumsan lacus vel facilisis.</p>
</div>
<div class="step on" style="left:855px">
  <svg width="40" height="40" viewBox="0 0 40 40" fill="none" stroke="#fff" stroke-width="2"><path d="M3 8h6l5 18h18l4-13H12"/><circle cx="16" cy="33" r="3"/><circle cx="30" cy="33" r="3"/><path d="M20 16l3 3 6-6"/></svg>
  <h4>Place Your Order and Activate Your Plan</h4><p>Risus commodo viverra aecenas accumsan lacus vel facilisis.</p>
</div>

<h2 class="sec-title" style="top:3432px">The Answer To All <span class="accent">Your Questions</span></h2>
<p class="sec-sub" style="top:3492px">Duis aute irure dolor in reprehenderit in voluptate velit esse<br>cillum dolore eu fugiat nulla pariatur.</p>
<div class="art" role="img" aria-label="Seated panda mascot beside a large phone showing a thirty dollar plan" style="left:91px;top:3550px;width:524px;height:524px;border-radius:45%;background:radial-gradient(ellipse at 45% 50%,#e4e4e4 0%,#7d7d7d 45%,rgba(255,255,255,0) 70%)"></div>

<div class="faq open" style="top:3578px"><div class="q"><span>Can I keep my current phone number?</span><span>–</span></div><div class="a">Yes! When you sign up, just select "Transfer my number" and we'll guide you through the simple steps.</div></div>
<div class="faq" style="top:3723px"><div class="q"><span>Does Tessel Mobile offer 5G?</span><span>+</span></div></div>
<div class="faq" style="top:3802px"><div class="q"><span>How do I activate my SIM or eSIM?</span><span>+</span></div></div>
<div class="faq" style="top:3881px"><div class="q"><span>Are there contracts or cancellation fees?</span><span>+</span></div></div>
<div class="btn" style="left:631px;top:3974px;width:152px;height:40px">View All</div>

<h2 class="sec-title" style="top:4152px">Our <span class="accent">Blog</span></h2>
<p class="sec-sub" style="top:4212px">Duis aute irure dolor in reprehenderit in voluptate velit esse<br>cillum dolore eu fugiat nulla pariatur.</p>
<div class="arrow" style="left:63px"><svg width="14" height="14" viewBox="0 0 14 14"><path d="M9 2L4 7l5 5" stroke="#fff" stroke-width="2" fill="none"/></svg></div>
<div class="arrow" style="left:1105px"><svg width="14" height="14" viewBox="0 0 14 14"><path d="M5 2l5 5-5 5" stroke="#fff" stroke-width="2" fill="none"/></svg></div>

<div class="post" style="left:111px"><div class="ph" role="img" aria-label="Close-up of hands holding a smartphone" style="background:linear-gradient(135deg,#5a3a26,#a0704c 55%,#2b1d14)"></div><h4>How to Switch to Tessel<br>Mobile in 3 Easy Steps</h4><p>Duis aute irure dolor in reprehenderit in voluptate velit esse cillum dolore eu fugiat nulla pariatur.</p><em>Read More ...</em></div>
<div class="post" style="left:442px"><div class="ph" role="img" aria-label="Man working at a laptop at his desk" style="background:linear-gradient(135deg,#d9dcdf,#7a8391 55%,#2f3a4f)"></div><h4>Best Budget Smartphones<br>for 2025</h4><p>Duis aute irure dolor in reprehenderit in voluptate velit esse cillum dolore eu fugiat nulla pariatur.</p><em>Read More ...</em></div>
<div class="post" style="left:772px"><div class="ph" role="img" aria-label="Woman smiling at her phone in a kitchen" style="background:linear-gradient(135deg,#efe6d6,#c9a978 55%,#6b5034)"></div><h4>What Does "Nationwide 5G"<br>Really Mean?</h4><p>Duis aute irure dolor in reprehenderit in voluptate velit esse cillum dolore eu fugiat nulla pariatur.</p><em>Read More ...</em></div>

<footer class="abs footer">
  <div class="fcol" style="left:111px"><h5>About Us</h5><p>Excepteur sint occaecat cupidatat non proident, sunt in culpa qui officia deserunt mollit anim id est laborum."</p>
    <div class="social"><i class="on"></i><i></i><i></i><i></i></div></div>
  <div class="fcol" style="left:442px"><h5>Quick Link</h5><a>Bring Your Own phone</a><a>Coverage Check</a><a>About Us</a><a>Support</a><a>Blog</a></div>
  <div class="fcol" style="left:684px"><h5>Service Features</h5><a>5G Coverage</a><a>What is 5G?</a><a>Family Phone Plans</a><a>Bring Your Own Phone</a><a>International Calling</a></div>
  <div class="fcol" style="left:944px"><h5>Support</h5><a>The Help Center</a><a>Order Status</a><a>Returns &amp; Exchanges</a><a>Unlock Policy</a><a>Phone Return Policy</a></div>
  <div class="copy">Copyright © 2025 Tessel Mobile. All rights reserved.</div>
</footer>

</body>
</html>
```